Podcast Art for Bright Belly Radio: Rising above Daily Flares

Read carefully Please. Most submittals so far have not read this.

We're looking for stunning, eye-catching, innovative yet simple podcast art for our first Podcast

Background should be solid, one color

Bright Belly Radio: Rising beyond Daily Flares
with Marcus Telford

Use our Brand Guide including logo, colors, and font
https://lnk.example-short.net/BBR2020StyleKit

Some Podcast Covers I like: https://casts.wavelane-audio.net/

Optional: Captain Flush graphic included above and/or my headshot uploaded below

As you can see humor / medutainment is part of the brand. As we are talking serious topic such as a disease many suffer from you can see the humor in the logo and "captain flush" . Here is the monologue for the first episode to give you a deeper feel on the content

https://files.papermoor-docs.net/doc/7qR_Lk2mWz9PdXc4VtBn8JhYs3FaEo6GuKwTn/edit?share=link

Target Market(s)

Those who suffer from gut issues, are diagnosed with inflammatory bowel disease(IBD), Crohn's Disease or Ulcerative Colitis - also their coaches, doctors, practitioners so functional or integrative medicine doctors/coaches, gastroenterologists etc.

Industry/Entity Type

Health And Wellness

Font styles to use
Other font styles liked:
• Primary: Oswald bold. Secondary: Oswald Medium or light

Requirements
Must have
• 3000 x 3000 pixels
Simple and eye-catching
Brand Guide Logo
Brand Guide Font
Brand Guide Colors including accent color(s)
I did not select colors below because I have included our Brand guide. Please use the exact colors there.
Nice to have
• Maybe my headshot and/or the captain flush graphic - if not too busy and still looks good
Should not have
• - Look busy
- Reverse Logo
- Not follow the Brand Guide
- Anything in the background but one solid color from the brief

```html
<!DOCTYPE html>
<html lang="en">
<head>
<meta charset="utf-8">
<title>Bright Belly Radio: Rising beyond Daily Flares</title>
<link rel="stylesheet" href="https://fonts.googleapis.com/css2?family=Oswald:wght@500;700&display=swap">
<style>
  :root {
    --pink: #d93a82;
    --navy: #27417a;
    --ice: #c6e6f1;
    --butter: #f6df7c;
    --photo-tone: #b8a89a;
  }
  * { margin: 0; padding: 0; box-sizing: border-box; }
  html, body { width: 1200px; height: 1200px; overflow: hidden; }
  body { font-family: "Oswald", "Arial Narrow", sans-serif; }
  .cover {
    position: relative;
    width: 1200px;
    height: 1200px;
    background: var(--navy);
    overflow: hidden;
  }
  .brand-panel {
    position: absolute;
    left: 0; top: 0;
    width: 428px; height: 1200px;
    background: var(--pink);
  }
  .divider {
    position: absolute;
    left: 428px; top: 0;
    width: 7px; height: 1200px;
    background: var(--butter);
  }
  .brand-name {
    position: absolute;
    left: 0; top: 0;
    width: 428px; height: 1200px;
    display: flex;
    flex-direction: column;
    align-items: center;
    justify-content: center;
    gap: 6px;
  }
  .brand-name .mark {
    width: 70px; height: 70px;
    border-radius: 50%;
    background: var(--ice);
    margin-bottom: 22px;
  }
  .brand-name span {
    display: block;
    color: var(--ice);
    font-weight: 700;
    font-size: 96px;
    line-height: 1;
    text-transform: uppercase;
    letter-spacing: 1px;
  }
  .show-title {
    position: absolute;
    left: 512px; top: 22px;
    color: var(--ice);
    font-weight: 700;
  }
  .show-title .big {
    display: block;
    font-size: 228px;
    line-height: 196px;
    letter-spacing: -1px;
  }
  .show-title .small {
    display: block;
    font-size: 70px;
    line-height: 80px;
    margin: 6px 0 8px 12px;
  }
  .host {
    position: absolute;
    left: 518px; top: 940px;
    color: var(--butter);
    font-weight: 500;
    text-transform: uppercase;
    line-height: 1;
  }
  .host .lead { display: block; font-size: 34px; letter-spacing: 2px; }
  .host .first { display: block; font-size: 62px; letter-spacing: 3px; margin-top: 10px; }
  .host .last { display: block; font-size: 50px; letter-spacing: 2px; margin-top: 8px; }
  .host-photo {
    position: absolute;
    left: 808px; top: 800px;
    width: 302px; height: 302px;
    border: 7px solid var(--pink);
    background: linear-gradient(160deg, #c9bcae 0%, var(--photo-tone) 55%, #e8e4df 100%);
  }
</style>
</head>
<body>
  <main class="cover">
    <div class="brand-panel"></div>
    <div class="divider"></div>
    <div class="brand-name">
      <div class="mark"></div>
      <span>Bright</span>
      <span>Belly</span>
      <span>Radio</span>
    </div>
    <h1 class="show-title">
      <span class="big">Rising</span>
      <span class="small">beyond</span>
      <span class="big">Daily</span>
      <span class="big">Flares</span>
    </h1>
    <p class="host">
      <span class="lead">With</span>
      <span class="first">Marcus</span>
      <span class="last">Telford</span>
    </p>
    <div class="host-photo" role="img" aria-label="Headshot of host Marcus Telford in a white shirt against a stone wall"></div>
  </main>
</body>
</html>
```